Church Website with Home Page and Member Sermon Library

I am in need of an updated design for our church website. This will include 4 pages (outlined below). We are a conservative, evangelical, Christian church. The site should be modern and clean, while still reflecting our conservative values. I already have a logo for our church, and I want the site to incorporate the logo, and match the logo/branding. Stock photos are allowed if needed, but I have uploaded some images of our church and would prefer those images to be used if possible. Any stock photos used should not include any people in the photos (scenery, nature, buildings, animals, etc. are fine).

The site will need 4 pages: Home, Support Us (Donate), Login, and Recording Library.

Page 1: Home
The home page should include the following sections:

- Navigation: Should include links to each section of the home page plus a "listen live" link which will take the user to a live-streaming site and a "support us" link which will take the user to a support/donate page.

- Announcements: Can be either a banner or some other design, but there needs to be some way for us to post announcements for visitors to see. I'm open for creative ideas in this section, but would like it not to take up a lot of room on the page.

- About Us: Should include address, service times (see attached document), and information about the church.

- Pastor Bio: A section that introduces our pastor and gives a short bio about our pastor. Would like this section to include a picture of our pastor. Somewhere in this section I would like to include this Bible reference: "And I will give you pastors according to mine heart, which shall feed you with knowledge and understanding. Jer 3:15 LPW"

- Articles of Faith (What We Believe): This should include several sub-sections each with a heading, body, and possibly 1 or more scripture references. I have attached a document to the brief that includes our articles of faith. Feel free to be creative with this section in how you lay these out and format them.

- Support Us: A small section that explains what kind of support someone can give and a link to a donation page. The link can say something like "Support Us" or "Donate Now".

- Contact form: A contact form that allows the visitor to send us a message. The contact form should ask for name, email, phone, and message.

- Footer: A footer that will be displayed on all pages of the site. This should include at a minimum a link to the home page (or a link to each individual section in the home page if you prefer), a link to "listen live", a link to "support us", a link to "contact us" (or you can put the contact form directly in the footer if you prefer), the address, and a "member login" link.

Page 2: Support Us
The donation page should include a form the visitor can fill out to make a donation. We will embed a third party form later. For this design, please just mock out the design with a basic form asking for name, phone, and email.

Page 3: Login
The recording library (detailed below) will require members to login with a shared numeric code before accessing the page. We need a design for a login screen. The screen should include navigation/footer just like all other pages, but the body of the login page will consist only of a form that asks the user to enter the access code and then a "login" button.

Page 4: Recording Library

The library page is a member-only page that will require a shared, numeric pass code to access. On this page, members will be able to access a filterable list of past sermons. The page by default should display most recent sermons, but should also include a search form that allows the member to filter the sermon list to find a particular sermon. The search form should allow the user to select a filter type (e.g. Speaker name, date, event, etc.) and type in a value to search. They should be able to add multiple filters and remove filters that have been added. Each sermon that is displayed in the result list should include basic information such as title, date, speaker, tags, etc. along with a download icon, and an embedded audio player where they can click a play button to stream it on-demand. Each sermon should also have clickable tags associated with it that can be used to find related sermons.
Updates

I have uploaded several images of our church. Feel free to incorporate these into your design if possible.

Target Market(s)

Church Members

Industry/Entity Type

Religion

Number of Pages Required

4 page

Font styles to use
Sans Serif

Colors

Designer to choose colors to be used in the design.

Requirements
Must have
• Must incorporate the logo (attached)
Nice to have
• Would like the design to incorporate pictures of our church (attached) instead of stock photos if possible.
Should not have
• Please avoid an overly cluttered design. Stock photos used should not include any people in the photos.

```html
<!DOCTYPE html>
<html lang="en">
<head>
<meta charset="utf-8">
<title>Grace Harbor Church</title>
<link href="https://fonts.googleapis.com/css2?family=Cinzel:wght@400;500&family=Montserrat:ital,wght@0,400;0,500;0,700;1,400&display=swap" rel="stylesheet">
<style>
:root{
  --blue:#3aa9c8;
  --green:#7ba65f;
  --navy:#4b6b8c;
  --ink:#2c2c2c;
  --text:#666;
  --dark:#333333;
  --light:#f4f4f4;
}
*{box-sizing:border-box;margin:0;padding:0}
html,body{width:1200px;height:4542px;overflow:hidden}
body{position:relative;font-family:"Montserrat",sans-serif;color:var(--text);background:#fff}
.abs{position:absolute}
.serif{font-family:"Cinzel",serif;color:var(--ink);letter-spacing:.08em}
.rule{position:absolute;height:3px;background:var(--blue)}
p{font-size:12.5px;line-height:20px}
a{color:inherit}

/* brand name: one line, one colour, one weight, one plain circle */
.brand{position:absolute;display:flex;align-items:center;gap:10px;font-family:"Cinzel",serif;font-weight:400;color:var(--green);letter-spacing:.06em;white-space:nowrap}
.brand i{flex:none;border-radius:50%;background:var(--green)}

/* hero */
.hero{left:0;top:0;width:1200px;height:583px;background:linear-gradient(180deg,#f4f4f3 0%,#ecebea 40%,#b98f72 62%,#8d6a55 78%,#a9a59e 100%)}
.nav a{position:absolute;top:50px;font-size:14px;color:#222;text-decoration:none}
.hero-title{position:absolute;left:0;top:185px;width:1200px;text-align:center;font-family:"Cinzel",serif;font-weight:400;font-size:62px;letter-spacing:.08em;color:#1e1e1e}
.pill{position:absolute;height:64px;border-radius:32px;background:#f3f1e8;border:3px solid #d9e3cf;box-shadow:0 2px 6px rgba(0,0,0,.15);display:flex;align-items:center;gap:26px;padding-left:10px}
.pill .dot{width:44px;height:44px;border-radius:50%;background:var(--green);display:flex;align-items:center;justify-content:center}
.pill span{font-family:"Cinzel",serif;color:var(--green);font-size:15px;letter-spacing:.06em}

/* about */
.about-photo{left:205px;top:700px;width:310px;height:475px;border-radius:40px 40px 0 0;background:linear-gradient(180deg,#c4c0bb 0%,#b0785a 35%,#9c6b52 70%,#8b7a60 100%)}
.eyebrow{font-size:12px;color:var(--blue);letter-spacing:.08em}
.services li{list-style:none;font-size:13px;color:#222;height:26px;letter-spacing:.04em}
.services li i{font-style:normal;color:var(--green);font-size:11px;margin-right:8px}
.services b{font-weight:700}

/* announcements */
.ann-bg{left:195px;top:1287px;width:808px;height:326px;background:var(--light)}
.arrow-btn{width:36px;height:36px;border-radius:50%;background:#fff;box-shadow:0 1px 5px rgba(0,0,0,.15);display:flex;align-items:center;justify-content:center}

/* pastor */
.pastor{left:0;top:1595px;width:1200px;height:715px;background:linear-gradient(180deg,#fbf7f6 0%,#f3ebea 45%,#efe5e3 75%,#f7f1f0 100%)}
.portrait{left:469px;top:1770px;width:256px;height:256px;border-radius:50%;border:5px solid #fff;box-shadow:0 3px 10px rgba(0,0,0,.2);background:radial-gradient(circle at 50% 40%,#d8d2c8 0%,#a09484 45%,#2f2d2c 80%)}

/* articles */
.article h3{width:230px;font-family:"Cinzel",serif;font-weight:400;font-size:16px;color:#333;letter-spacing:.08em;line-height:22px;padding-left:16px;position:relative}
.article h3:before{content:"";position:absolute;left:0;top:8px;width:5px;height:5px;border-radius:50%;background:var(--green)}
.article p{font-size:11.5px;line-height:19.5px;color:#777;margin-top:12px;width:230px}
.article p u{color:#444}
.refs{list-style:none;margin-top:14px}
.refs li{font-size:10px;line-height:23px;color:#444}
.refs li i{font-style:normal;color:var(--green);font-size:11px;margin-right:6px}
.refs li u{font-style:italic}
.divider{width:230px;height:1px;background:#e3e3e3}

/* support + contact */
.support{left:0;top:3140px;width:1200px;height:730px;background:linear-gradient(180deg,#e9e7e4 0%,#cfc9c2 25%,#8a7464 50%,#5a4b42 75%,#333 100%)}
.dark{left:0;top:3870px;width:1200px;height:672px;background:var(--dark)}
.btn{position:absolute;background:var(--green);color:#fff;font-family:"Cinzel",serif;font-size:15px;letter-spacing:.06em;display:flex;align-items:center;justify-content:center;gap:10px}
.field{position:absolute;background:#fff;border:1px solid #cfcfcf;font-size:11px;color:#555;padding:14px 16px}
.links a{display:block;font-size:13px;color:#bbb;text-decoration:none;height:27px}
.social span{display:inline-block;width:10px;height:10px;border-radius:50%;background:#fff;margin-left:14px}
</style>
</head>
<body>

<!-- HERO -->
<section class="abs hero" role="img" aria-label="Photo of the brick church building under a pale sky"></section>
<div class="brand" style="left:136px;top:58px;font-size:24px"><i style="width:12px;height:12px"></i>Grace Harbor</div>
<nav class="nav">
  <a style="left:636px">About Us</a>
  <a style="left:763px">Articles Of Faith</a>
  <a style="left:940px">Contact Us</a>
</nav>
<h1 class="hero-title">KEEP FAITH ALWAYS</h1>
<div class="rule" style="left:535px;top:270px;width:130px"></div>
<div class="pill" style="left:490px;top:305px;width:222px">
  <div class="dot"><svg width="24" height="20" viewBox="0 0 24 20" fill="none" stroke="#fff" stroke-width="1.6"><circle cx="12" cy="8" r="2" fill="#fff"/><path d="M8 4a6 6 0 0 0 0 8M16 4a6 6 0 0 1 0 8M5 1a10 10 0 0 0 0 14M19 1a10 10 0 0 1 0 14"/></svg></div>
  <span>LISTEN LIVE</span>
</div>

<!-- ABOUT -->
<div class="abs about-photo" role="img" aria-label="Photo of the brick church sign wall"></div>
<div class="abs" style="left:636px;top:690px;width:390px">
  <div class="eyebrow">ABOUT</div>
  <h2 class="serif" style="font-weight:400;font-size:23px;margin-top:8px">GRACE HARBOR CHURCH</h2>
  <p style="margin-top:14px">Ut diam tortor consectetur lacus scelerisque tortor congue viverra egestas. Tristique in consectetur leo arcu blandit diam et sed volutpat.</p>
  <p style="margin-top:8px">Aliquam at commodo venenatis quis. Velit neque interdum molestie risus consectetur vestibulum a eget. Ultricies volutpat orci eros quisque ullamcorper quis est.</p>
</div>
<div class="rule" style="left:636px;top:906px;width:148px"></div>
<div class="abs serif" style="left:636px;top:942px;font-size:16px;font-weight:500">LOCATION</div>
<div class="abs" style="left:636px;top:978px;font-size:12.5px;line-height:20px">
  <svg width="10" height="13" viewBox="0 0 10 13" style="vertical-align:-1px"><path d="M5 12S1 7 1 4.5a4 4 0 0 1 8 0C9 7 5 12 5 12z" fill="none" stroke="var(--green)" stroke-width="1.2"/><circle cx="5" cy="4.5" r="1.3" fill="var(--green)"/></svg>
  418 Maple Ridge Rd. Fairview,<br><span style="margin-left:19px">Ohio 43210</span>
</div>
<div class="abs serif" style="left:636px;top:1048px;font-size:16px;font-weight:500">SERVICE TIME ARE</div>
<ul class="abs services" style="left:636px;top:1082px">
  <li><i>01.</i>Wednesday Evening Service: &nbsp;<b>7:30 PM</b></li>
  <li><i>02.</i>Sunday School: &nbsp;<b>10:00 AM</b></li>
  <li><i>03.</i>Sunday Morning Service: <b>11:00 AM</b></li>
  <li><i>04.</i>Sunday Evening Service: &nbsp;<b>5:30 PM</b></li>
</ul>

<!-- ANNOUNCEMENTS -->
<div class="abs ann-bg"></div>
<svg class="abs" style="left:185px;top:1275px" width="830" height="350" viewBox="0 0 830 350" fill="none" stroke="var(--navy)">
  <path d="M345 10H30Q30 30 10 30V320Q30 320 30 340H800Q800 320 820 320V30Q800 30 800 10H485" stroke-width="6"/>
  <path d="M20 40Q40 40 40 20M810 40Q790 40 790 20M20 310Q40 310 40 330M810 310Q790 310 790 330" stroke-width="2" stroke="#8aa2bb"/>
</svg>
<div class="brand" style="left:535px;top:1274px;width:140px;justify-content:center;font-size:15px"><i style="width:8px;height:8px"></i>Grace Harbor</div>
<div class="abs serif" style="left:0;top:1368px;width:1200px;text-align:center;font-size:32px">ANNOUNCEMENTS</div>
<p class="abs" style="left:360px;top:1422px;width:480px;text-align:center;color:#333">Ullamcorper facilisi egestas semper fames suscipit penatibus amet. Ut diam tortor consectetur lacus scelerisque tortor congue viverra</p>
<div class="abs arrow-btn" style="left:226px;top:1434px"><svg width="10" height="14"><path d="M8 1L2 7l6 6" stroke="#333" fill="none" stroke-width="1.6"/></svg></div>
<div class="abs arrow-btn" style="left:934px;top:1434px"><svg width="10" height="14"><path d="M2 1l6 6-6 6" stroke="#333" fill="none" stroke-width="1.6"/></svg></div>
<div class="abs serif" style="left:380px;top:1490px;width:200px;text-align:right;font-size:17px">ANNOUNCEMENT</div>
<div class="abs serif" style="left:380px;top:1526px;width:200px;text-align:right;font-size:10px;color:#777">FABRUARY 16TH</div>
<div class="abs" style="left:600px;top:1488px;width:1px;height:52px;background:#bbb"></div>
<div class="abs serif" style="left:622px;top:1490px;font-size:12px;line-height:15px;color:#444">GRACE HARBOR<br>CHURCH</div>
<div class="abs" style="left:622px;top:1524px;font-size:11.5px;font-style:italic;color:#333">Pastor Daniel Reed</div>
<div class="abs" style="left:573px;top:1573px;display:flex;gap:6px;align-items:center">
  <span style="width:4px;height:4px;border-radius:50%;background:#ccc"></span><span style="width:4px;height:4px;border-radius:50%;background:#ccc"></span>
  <span style="width:10px;height:10px;border-radius:50%;border:1px solid #999;background:#ccc"></span>
  <span style="width:4px;height:4px;border-radius:50%;background:#ccc"></span><span style="width:4px;height:4px;border-radius:50%;background:#ccc"></span>
</div>

<!-- PASTOR -->
<section class="abs pastor" role="img" aria-label="Soft blurred photo of the church sanctuary pews"></section>
<div class="abs serif" style="left:0;top:1692px;width:1200px;text-align:center;font-size:30px">OUR PASTOR</div>
<div class="abs" style="left:180px;top:1792px;width:245px">
  <p>Ullamcorper facilisi egestas semper fames suscipit penatibus amet. Ut diam tortor consectetur lacus scelerisque tortor congue viverra egestas. Tristique in consectetur leo arcu blandit diam et sed volutpat.</p>
  <p style="margin-top:16px">Aliquam at commodo venenatis quis. Velit neque interdum molestie risus consectetur vestibulum a eget.</p>
</div>
<div class="abs portrait" role="img" aria-label="Portrait photo of the pastor"></div>
<div class="abs" style="left:760px;top:1792px;width:245px">
  <p>Ut diam tortor consectetur lacus scelerisque tortor congue viverra egestas. Tristique in consectetur leo arcu blandit diam et sed volutpat.</p>
  <p style="margin-top:16px">Aliquam at commodo venenatis quis. Velit neque interdum molestie risus consectetur vestibulum a eget.</p>
</div>
<div class="abs" style="left:0;top:2040px;width:1200px;text-align:center;font-size:8px;color:#333;letter-spacing:.05em">PASTOR</div>
<div class="abs serif" style="left:0;top:2053px;width:1200px;text-align:center;font-size:17px;letter-spacing:.04em">DANIEL REED</div>
<div class="abs" style="left:290px;top:2108px;width:620px;text-align:center;font-size:16px;line-height:26px;font-style:italic;color:#555">“And I will give you pastors according to mine heart, which shall feed you with knowledge and understanding.”</div>
<div class="abs serif" style="left:0;top:2186px;width:1200px;text-align:center;font-size:18px;letter-spacing:.02em;color:#444">JER 3:15 LPW</div>

<!-- ARTICLES OF FAITH -->
<div class="abs serif" style="left:0;top:2410px;width:1200px;text-align:center;font-size:32px">ARTICLES OF FAITH</div>
<div class="rule" style="left:550px;top:2462px;width:100px"></div>

<div class="abs article" style="left:190px;top:2510px">
  <h3>THE GOD HEAD.</h3>
  <p>We believe in the God head bodily, known as the Divine Trinity. This body consist of God the father, Jesus Christ, his only begotten son and the redeemer of the world, and the Holy Ghost, The third person of the Holy Trinity</p>
</div>
<div class="abs article" style="left:190px;top:2770px">
  <h3>BAPTISM OF THE HOLY GHOST.</h3>
  <p>We believe in the baptism of the Holy Ghost as it is taught in the Bible and promised by our Lord Jesus Christ, with speaking in tongues as the Spirit gives utterance as the initial evidence. <u>Acts 2:4</u> we believe that the gift of the Holy Ghost is for all believers as the Lord promised. <u><i>Acts 2:17-18</i></u></p>
</div>

<div class="abs article" style="left:477px;top:2510px">
  <h3>FULL SALVATION.</h3>
  <p>We believe that Salvation is received only when a person comes to the realization that he or she is lost and separated from God and becomes full of godly sorrow, confessing their sins and true repentance, believing in the shed blood of the Lord Jesus Christ as the only sacrifice for sins. Through the blood of Christ we have:</p>
  <ul class="refs">
    <li><i>01.</i><u>Remission of sins, Matthew 26:28 Heb 9:22</u></li>
    <li><i>02.</i><u>Sanctification, Hebrews 13:12</u></li>
    <li><i>03.</i><u>Redemption, Revelations 5:9</u></li>
    <li><i>04.</i><u>Cleansing, 1 John 1:7 Rev. 1:5</u></li>
    <li><i>05.</i><u>Justification, Romans 5:9</u></li>
  </ul>
  <div class="divider" style="margin-top:8px"></div>
</div>
<div class="abs article" style="left:477px;top:2924px">
  <h3>SECOND COMING OF CHRIST.</h3>
  <p>We believe in the second coming of Jesus Christ. <u><i>Matthew 24:44 Luke 12:40</i></u></p>
  <div class="divider" style="margin-top:16px"></div>
</div>

<div class="abs article" style="left:780px;top:2510px">
  <h3>SANCTIFICATION</h3>
  <p>“Sanctify them through thy truth thy word is truth <u><i>St John 17:17.</i></u> For this is the will of God even your sanctification”</p>
  <p style="margin-top:8px">We believe in a set apart life, separate from the world to Christ <u><i>2 Cor 6:17-18</i></u></p>
  <div class="divider" style="margin-top:22px"></div>
</div>
<div class="abs article" style="left:780px;top:2758px">
  <h3>DIVINE HEALING.</h3>
  <p>We believe Divine Healing to be included in the atonement of Jesus Christ our Lord, And believe that it is still for us today. <u><i>1 Peter 2:24 Luke 9:1-2 Mark 16-18 James 5:15</i></u></p>
  <div class="divider" style="margin-top:20px"></div>
</div>
<div class="abs article" style="left:780px;top:2964px">
  <h3>ETERNITY</h3>
  <p style="margin-top:24px">We believe in Literal Eternity. Eternal Life for the believer and eternal death for those without Christ. <u><i>Revelations 21:1-27</i></u></p>
  <div class="divider" style="margin-top:14px"></div>
</div>

<!-- SUPPORT -->
<section class="abs support" role="img" aria-label="Photo of the church building fading into shadow"></section>
<div class="abs serif" style="left:0;top:3212px;width:1200px;text-align:center;font-size:32px">SUPPORT OUR MINISTRY</div>
<div class="rule" style="left:550px;top:3263px;width:100px"></div>
<p class="abs" style="left:278px;top:3290px;width:644px;text-align:center;color:#333">Ut diam tortor consectetur lacus scelerisque tortor congue viverra egestas. Tristique in consectetur leo arcu blandit diam et sed volutpat. Aliquam at commodo venenatis quis. Velit neque interdum molestie risus consectetur vestibulum a eget. Ultricies volutpat orci eros quisque ullamcorper quis est.</p>
<div class="btn" style="left:525px;top:3390px;width:148px;height:42px">
  <svg width="18" height="16" viewBox="0 0 18 16" fill="none" stroke="#fff" stroke-width="1.3"><path d="M1 10h4l4 2h5l3-3M5 10v5H1v-5M9 3a2.5 2.5 0 1 0 5 0 2.5 2.5 0 1 0-5 0"/></svg>SUPPORT US
</div>

<!-- CONTACT -->
<div class="abs dark"></div>
<div class="abs serif" style="left:0;top:3745px;width:1200px;text-align:center;font-size:32px;color:#fff">CONTACT US</div>
<div class="rule" style="left:550px;top:3799px;width:100px"></div>
<div class="field" style="left:176px;top:3843px;width:414px;height:42px">Name *</div>
<div class="field" style="left:610px;top:3843px;width:412px;height:42px">Phone *</div>
<div class="field" style="left:176px;top:3900px;width:846px;height:42px">Email address *</div>
<div class="field" style="left:176px;top:3956px;width:846px;height:96px">Message</div>
<div class="btn" style="left:535px;top:4085px;width:135px;height:46px">SEND US
  <svg width="20" height="10"><path d="M0 5h18M14 1l4 4-4 4" stroke="#fff" fill="none" stroke-width="1.3"/></svg>
</div>

<!-- FOOTER -->
<div class="pill" style="left:178px;top:4275px;width:220px">
  <div class="dot"><svg width="24" height="20" viewBox="0 0 24 20" fill="none" stroke="#fff" stroke-width="1.6"><circle cx="12" cy="8" r="2" fill="#fff"/><path d="M8 4a6 6 0 0 0 0 8M16 4a6 6 0 0 1 0 8M5 1a10 10 0 0 0 0 14M19 1a10 10 0 0 1 0 14"/></svg></div>
  <span>LISTEN LIVE</span>
</div>
<div class="abs serif" style="left:185px;top:4376px;font-size:14px;color:#eee">LOCATION</div>
<div class="abs" style="left:185px;top:4403px;font-size:12.5px;line-height:17px;color:#ccc">
  <svg width="10" height="13" viewBox="0 0 10 13" style="vertical-align:-1px"><path d="M5 12S1 7 1 4.5a4 4 0 0 1 8 0C9 7 5 12 5 12z" fill="none" stroke="var(--green)" stroke-width="1.2"/><circle cx="5" cy="4.5" r="1.3" fill="var(--green)"/></svg>
  418 Maple Ridge Rd. Fairview,<br><span style="margin-left:19px">Ohio 43210</span>
</div>
<div class="brand" style="left:460px;top:4372px;width:280px;justify-content:center;font-size:28px"><i style="width:14px;height:14px"></i>Grace Harbor</div>
<div class="abs serif" style="left:824px;top:4268px;font-size:14px;color:#ddd">QUICK LINKS</div>
<nav class="abs links" style="left:824px;top:4305px">
  <a>About Us</a><a>Articles Of Faith</a><a>Support Our Ministry</a><a>Contact Us</a><a>Member Login</a>
</nav>
<div class="abs" style="left:176px;top:4504px;font-size:11px;color:#ddd">Copyright 2023 Grace Harbor Church | All rights reserved</div>
<div class="abs social" style="left:900px;top:4501px"><span></span><span></span><span></span><span></span></div>

</body>
</html>
```